Yacht, Boats, Watersports company needs a redesign of business card

Hello Designers!
We are a Boat dealership company that sells fun in the water, we sell boats, Yachts, Kayaks and also yacht WaterSport toys. We are looking to redesign our business cards in to something a little bit more sophisticated. in a way that we can make better use of our company colors. I'm attaching a zipped file containing the company 3 sets of company logo which one is an horizontal another one is a vertical and also a chromed 3d logo. Also is included two set of business cards that we use and also some designs that i think it's interesting. We use PMS 2026c Orange and PMS 7687C Blue. I would like to see at least two different options with the orange as accent and also using blue as an accent color. It's really important for the business cards to have a font option and size that is legible to most people. Our current website is wwww.coralpennant.com. Please visit if you want to have a better feeling of the Boat dealership
You can send Single sided or double side options. We are now using single sided but we may be open for a double side option if we really like the design.
Target Market(s)
Marine, boat sales, yacht sales, water toys sales/
Contact Information for Business Card
Name: Dale Whitcombe
Address: 212 North Fenwick Lane,
Harbor Point, FL 33117
Phone: 954-731-8842
Fax: 954:731-8843
Cell: 954-382-1490
Email: dw@coralpennant.com
Website: coralpennant.com
Requirements
Must have
- the current information of the business card provided.
logo
use the PMS Colors
Nice to have
- a touch of elegance and sophistication but simple
Should not have
- should not have any typography that is hard to read, the card should be simple but yet sophisticated.

```html
<!DOCTYPE html>
<html lang="en">
<head>
<meta charset="utf-8">
<title>Coral Pennant – Business Card</title>
<link href="https://fonts.googleapis.com/css2?family=Oswald:wght@700&family=Roboto:wght@400;700&display=swap" rel="stylesheet">
<style>
  :root {
    --navy: #0f4577;
    --orange: #e85d2c;
    --paper: #f4f4f4;
    --white: #ffffff;
    --backdrop: #e4e4e4;
  }
  * { margin: 0; padding: 0; box-sizing: border-box; }
  html, body { width: 1200px; height: 960px; overflow: hidden; }
  body {
    background: radial-gradient(ellipse at center, #f1f1f1 0%, var(--backdrop) 70%, #d9d9d9 100%);
    font-family: "Roboto", Arial, sans-serif;
    position: relative;
  }
  .card {
    position: absolute;
    left: 307px;
    width: 590px;
    height: 335px;
    overflow: hidden;
    box-shadow: 2px 3px 5px rgba(0,0,0,0.35);
  }
  /* Front */
  .card-front { top: 118px; background: var(--navy); }
  .front-mark {
    position: absolute; left: 245px; top: 77px;
    width: 100px; height: 100px;
  }
  .wordmark {
    font-family: "Roboto", Arial, sans-serif;
    font-weight: 700;
    text-transform: uppercase;
    white-space: nowrap;
  }
  .front-wordmark {
    position: absolute; left: 0; right: 0; top: 196px;
    text-align: center; font-size: 32px; letter-spacing: 7px; color: var(--white);
  }
  .front-website {
    position: absolute; left: 0; right: 0; top: 284px;
    text-align: center; font-size: 15px; letter-spacing: 1.8px; color: var(--white);
  }
  .front-notch {
    position: absolute; left: 275px; bottom: 0;
    width: 40px; height: 26px;
  }
  /* Back */
  .card-back { top: 505px; background: var(--navy); }
  .back-top {
    position: absolute; left: 0; top: 0; width: 100%; height: 166px;
    background: var(--paper);
    border-bottom: 2px solid var(--orange);
  }
  .back-wordmark {
    position: absolute; left: 50px; top: 35px;
    font-size: 26px; letter-spacing: 6px; color: var(--navy);
  }
  .holder-name {
    position: absolute; left: 50px; top: 120px;
    font-family: "Oswald", "Arial Narrow", sans-serif;
    font-weight: 700; font-size: 25px; line-height: 1;
    text-transform: uppercase; color: var(--navy);
  }
  .holder-name .surname { color: var(--orange); }
  .back-pointer {
    position: absolute; left: 0; top: 147px; width: 28px; height: 40px;
  }
  .contact-list {
    position: absolute; left: 50px; top: 196px;
    list-style: none; color: var(--white); font-size: 16px; line-height: 19.5px;
  }
  .contact-list li { display: flex; align-items: center; gap: 5px; }
  .contact-list svg { width: 14px; height: 13px; flex: none; }
  .address {
    position: absolute; left: 50px; top: 285px;
    color: var(--white); font-size: 16px;
  }
  .back-seal {
    position: absolute; left: 372px; top: 80px; width: 180px; height: 180px;
  }
</style>
</head>
<body>

  <section class="card card-front" aria-label="Card front">
    <svg class="front-mark" viewBox="0 0 100 100" aria-hidden="true">
      <circle cx="50" cy="50" r="46" fill="none" stroke="var(--orange)" stroke-width="6"/>
    </svg>
    <div class="wordmark front-wordmark">Coral Pennant</div>
    <div class="front-website">coralpennant.com</div>
    <svg class="front-notch" viewBox="0 0 40 26" aria-hidden="true">
      <polygon points="20,0 40,26 0,26" fill="var(--orange)"/>
    </svg>
  </section>

  <section class="card card-back" aria-label="Card back">
    <div class="back-top"></div>
    <div class="wordmark back-wordmark">Coral Pennant</div>
    <h1 class="holder-name">Dale <span class="surname">Whitcombe</span></h1>
    <svg class="back-pointer" viewBox="0 0 28 40" aria-hidden="true">
      <polygon points="0,0 28,20 0,40" fill="var(--orange)"/>
    </svg>

    <ul class="contact-list">
      <li>
        <svg viewBox="0 0 14 14" aria-hidden="true"><path d="M3 1l2.5 3-1.3 1.5c.8 1.7 2.2 3.1 3.8 3.8L9.5 8 13 10.5 11.5 13C6 12.5 1.5 8 1 2.5z" fill="var(--orange)"/></svg>
        954-731-8842
      </li>
      <li>
        <svg viewBox="0 0 14 14" aria-hidden="true"><rect x="3.5" y="1" width="7" height="3.5" fill="var(--orange)"/><rect x="1" y="5" width="12" height="5.5" rx="1" fill="var(--orange)"/><rect x="3.5" y="9" width="7" height="4" fill="var(--orange)" stroke="var(--navy)" stroke-width="0.8"/></svg>
        954:731-8843
      </li>
      <li>
        <svg viewBox="0 0 14 14" aria-hidden="true"><rect x="4" y="0.8" width="6.5" height="12.4" rx="1" fill="none" stroke="var(--orange)" stroke-width="1.2"/><circle cx="7.25" cy="11" r="0.7" fill="var(--orange)"/></svg>
        954-382-1490
      </li>
      <li>
        <svg viewBox="0 0 14 14" aria-hidden="true"><rect x="1" y="3" width="12" height="8.5" fill="none" stroke="var(--orange)" stroke-width="1.2"/><path d="M1 3l6 5 6-5" fill="none" stroke="var(--orange)" stroke-width="1.2"/></svg>
        dw@coralpennant.com
      </li>
    </ul>
    <p class="address">212 North Fenwick Lane, Harbor Point, FL 33117</p>

    <svg class="back-seal" viewBox="0 0 180 180" aria-hidden="true">
      <circle cx="90" cy="90" r="88" fill="var(--white)"/>
      <circle cx="90" cy="90" r="76" fill="none" stroke="var(--orange)" stroke-width="8"/>
    </svg>
  </section>

</body>
</html>
```